Brightmoor Lift Inc Website Deisgn

We are a new small elevator contracting company.
We would like a full website designed similar to
http://pellingtonlifts.com or https://www.northvalelifting.ca/
In addition to contents found on the above webpages.. we would like a section for project gallery etc.... have fun with it ... make it professional

Target Market(s)

Elevator Consultants - Property managers - Condo Boards - Commercial office buildings

Coding

Number of Pages Required

5+ page

Requirements
Must have
• Navigation Bar.. Be view able via mobile ..Should be pictures of Tall Office buildings in background.. Toronto city skyline etc....

Have Fun!

```html
<!DOCTYPE html>
<html lang="en">
<head>
<meta charset="utf-8">
<title>Brightmoor Lift Inc</title>
<link href="https://fonts.googleapis.com/css2?family=Oswald:wght@200;300;400;500&family=Open+Sans:wght@400;600&display=swap" rel="stylesheet">
<style>
:root{
  --orange:#ff6a00;
  --orange-light:#ff8a1f;
  --ink:#2b2b2b;
  --text:#4a4a4a;
  --dark:#3a3a3a;
  --card:#1f1f1f;
  --black:#0b0b0b;
  --bar:#1c1c1c;
  --white:#ffffff;
  --muted:#9a9a9a;
  --grey-light:#c9c9c9;
}
*{box-sizing:border-box;margin:0;padding:0}
html,body{width:1200px;height:3397px;overflow:hidden;background:var(--white)}
body{position:relative;font-family:"Open Sans",Arial,sans-serif;color:var(--text)}
.abs{position:absolute}
.head{font-family:"Oswald",Arial,sans-serif;text-transform:uppercase;color:var(--ink);font-weight:400}

/* hero */
.hero{left:0;top:0;width:1200px;height:730px;clip-path:polygon(0 0,100% 0,100% 620px,50% 730px,0 620px);
  background:linear-gradient(180deg,#5a5a5a 0%,#3d3d3d 30%,#262626 45%,#4a4a4a 60%,#1e1e1e 100%)}
.brand{left:62px;top:24px;display:flex;align-items:center;gap:9px;color:var(--white);font-family:"Oswald",sans-serif;font-weight:500;font-size:22px;letter-spacing:.5px;white-space:nowrap;line-height:1}
.brand-dot{width:40px;height:40px;border:4px solid var(--white);border-radius:50%;flex:none}
.nav{left:352px;top:34px;display:flex;gap:43px;font-family:"Oswald",sans-serif;font-weight:300;font-size:17px;color:var(--white);text-transform:uppercase;white-space:nowrap}
.nav .active{border-bottom:2px solid var(--white);padding-bottom:8px}
.nav-phone{left:993px;top:32px;color:var(--white);font-family:"Oswald",sans-serif;font-size:19px;display:flex;align-items:center;gap:8px;white-space:nowrap}
.hero-title{left:0;width:1200px;top:246px;text-align:center;color:var(--white);font-family:"Oswald",sans-serif;font-weight:500;font-size:74px;letter-spacing:4px;line-height:1}
.hero-sub{left:0;width:1200px;top:322px;text-align:center;color:var(--white);font-family:"Oswald",sans-serif;font-weight:200;font-size:56px;letter-spacing:5px;line-height:1}
.btn-orange{background:linear-gradient(90deg,var(--orange-light),var(--orange));color:var(--white);font-family:"Oswald",sans-serif;text-transform:uppercase;display:flex;align-items:center;justify-content:center}
.hero-cta{left:498px;top:409px;width:199px;height:60px;font-size:23px}
.arrow{width:52px;height:52px;border-radius:50%;background:rgba(200,200,200,.55);display:flex;align-items:center;justify-content:center}

/* about */
.about-photo{left:169px;top:780px;width:338px;height:338px;border-radius:50%;background:radial-gradient(circle,#d8d8d8 0%,#8a8a8a 55%,#3a3a3a 100%)}
.about-title{left:587px;top:804px;font-size:40px;font-weight:500}
.about-text{left:589px;top:876px;width:520px;font-size:17px;line-height:23px}
.about-text p+p{margin-top:28px}
.btn-outline{left:589px;top:1072px;width:151px;height:44px;border:3px solid var(--orange);color:var(--orange);font-family:"Oswald",sans-serif;font-size:17px;display:flex;align-items:center;justify-content:center}

/* services */
.services-edge{left:0;top:1176px;width:1200px;height:680px;background:var(--grey-light);clip-path:polygon(0 85px,50% 0,100% 50px,100% 590px,50% 677px,0 590px)}
.services{left:0;top:1176px;width:1200px;height:677px;clip-path:polygon(0 83px,50% 0,100% 83px,100% 560px,50% 677px,0 592px);
  background:linear-gradient(180deg,#4a4a4a 0%,#3c3c3c 55%,#5c5c5c 85%,#707070 100%)}
.services-title{left:0;width:1200px;top:1238px;text-align:center;color:var(--white);font-size:40px;font-weight:500}
.card{top:1328px;width:319px;height:399px;background:var(--card)}
.card-photo{width:319px;height:204px}
.card h3{color:var(--white);font-family:"Oswald",sans-serif;font-weight:400;font-size:22px;text-align:center;margin-top:22px;text-transform:uppercase}
.card p{color:#b5b5b5;font-size:12.5px;line-height:19px;text-align:center;width:260px;margin:10px auto 0}
.card .btn-white{margin:16px auto 0;width:146px;height:39px;border:2px solid var(--white);color:var(--white);font-family:"Oswald",sans-serif;font-size:16px;display:flex;align-items:center;justify-content:center;text-transform:uppercase}

/* gallery */
.gallery-title{left:0;width:1200px;top:1900px;text-align:center;font-size:40px;font-weight:500}
.gallery{left:105px;top:1978px;display:grid;grid-template-columns:repeat(3,328px);grid-template-rows:repeat(2,222px);gap:7px}
.gallery div{width:100%;height:100%}

/* contact */
.contact-band{left:0;top:2519px;width:1200px;height:514px;clip-path:polygon(0 85px,50% 0,100% 85px,100% 421px,50% 514px,0 421px);
  background:linear-gradient(180deg,#dcdcdc 0%,#a9a9a9 40%,#6b6b6b 75%,#3e3e3e 100%)}
.contact-box{left:345px;top:2614px;width:504px;height:267px;background:rgba(245,245,245,.95);text-align:center}
.contact-box h2{font-size:40px;font-weight:500;margin-top:36px;line-height:1}
.contact-box p{font-size:16px;line-height:20px;color:var(--ink);width:420px;margin:12px auto 0}
.contact-box .btn-orange{width:174px;height:40px;margin:16px auto 0;font-size:19px}
.contact-box .call{font-weight:600;font-size:17px;color:var(--ink);margin-top:14px}

/* footer */
.footer{left:0;top:2940px;width:1200px;height:397px;background:var(--black);clip-path:polygon(0 0,50% 93px,100% 0,100% 100%,0 100%)}
.footer-brand{left:115px;top:3092px;display:flex;align-items:center;gap:9px;color:var(--white);font-family:"Oswald",sans-serif;font-weight:500;font-size:24px;letter-spacing:.5px;white-space:nowrap;line-height:1}
.footer-brand .brand-dot{width:48px;height:48px}
.footer-about{left:119px;top:3166px;width:260px;color:#cfcfcf;font-size:13px;line-height:19px}
.f-title{color:var(--white);font-family:"Oswald",sans-serif;font-size:21px;font-weight:400;text-transform:uppercase}
.f-list{color:#d7d7d7;font-size:13.5px}
.contact-list li{list-style:none;display:flex;align-items:center;gap:10px;height:34px;white-space:nowrap}
.company-list li{list-style:none;height:27px;line-height:27px}
.sub-input{left:890px;top:3125px;width:224px;height:37px;background:#232323;display:flex}
.sub-input span{flex:1;color:#bdbdbd;font-size:11px;padding:11px 16px}
.sub-input i{width:31px;background:var(--orange);display:flex;align-items:center;justify-content:center}
.social{top:3188px;width:28px;height:28px;border-radius:50%;border:2px solid var(--white)}
.bottom-bar{left:0;top:3337px;width:1200px;height:60px;background:var(--bar);color:#a6a6a6;font-size:13.5px;text-align:center;line-height:60px}
</style>
</head>
<body>

<section class="abs hero" role="img" aria-label="Black and white city skyline at night reflected in the lake"></section>
<div class="abs brand"><span class="brand-dot"></span>BRIGHTMOOR LIFT INC</div>
<nav class="abs nav">
  <span class="active">Home</span><span>About Us</span><span>Our Services</span><span>Free Quote</span><span>Gallery</span><span>Contact</span>
</nav>
<div class="abs nav-phone">
  <svg width="20" height="20" viewBox="0 0 24 24"><path fill="#ff6a00" d="M6.6 10.8a15 15 0 0 0 6.6 6.6l2.2-2.2c.3-.3.7-.4 1-.2 1.1.4 2.3.6 3.6.6.6 0 1 .4 1 1V20c0 .6-.4 1-1 1A17 17 0 0 1 3 4c0-.6.4-1 1-1h3.5c.6 0 1 .4 1 1 0 1.3.2 2.5.6 3.6.1.3 0 .7-.2 1z"/></svg>
  (416) 555 0182
</div>
<h1 class="abs hero-title">BRIGHTMOOR LIFT</h1>
<div class="abs hero-sub">SERVICE CONTRACTING</div>
<div class="abs btn-orange hero-cta">Contact Us</div>
<div class="abs arrow" style="left:35px;top:339px"><svg width="16" height="16" viewBox="0 0 16 16"><path d="M10 2 4 8l6 6" fill="none" stroke="#222" stroke-width="2"/></svg></div>
<div class="abs arrow" style="left:1122px;top:339px"><svg width="16" height="16" viewBox="0 0 16 16"><path d="m6 2 6 6-6 6" fill="none" stroke="#222" stroke-width="2"/></svg></div>

<section>
  <div class="abs about-photo" role="img" aria-label="Circular black and white photo looking up an elevator shaft"></div>
  <h2 class="abs head about-title">Brightmoor Lift</h2>
  <div class="abs about-text">
    <p>Pellentesque faucibus Ut accumsan ultricies elit Maecenas at justo id velit placerat molestie Donec dictum lectus non odio Cras a ante vitae enim iaculis aliquam</p>
    <p>Mauris nunc quam venenatis nec euismod sit amet egestas placerat est Pellentesque habitant morbi tristique senectus et netus et malesuada fames ac turpis egestas Cras id elit</p>
  </div>
  <div class="abs btn-outline">LEARN MORE</div>
</section>

<div class="abs services-edge"></div>
<section class="abs services" role="img" aria-label="Dark grey city skyline backdrop"></section>
<h2 class="abs head services-title">Our Services</h2>
<article class="abs card" style="left:98px">
  <div class="card-photo" role="img" aria-label="Elevator car inside its shaft" style="background:linear-gradient(160deg,#5a4a3a,#2a2420 60%,#6b5d4c)"></div>
  <h3>Service &amp; Repair</h3>
  <p>consectetuer augue nisi quis lacus Ut ac mi quis lacus mollis aliquam Curabitur iaculis tempus eros Curabitur</p>
  <div class="btn-white">Learn More</div>
</article>
<article class="abs card" style="left:439px">
  <div class="card-photo" role="img" aria-label="Glass office towers against a blue sky" style="background:linear-gradient(160deg,#9ec7ef,#2f6fc2 50%,#173d80)"></div>
  <h3>Modernization</h3>
  <p>consectetuer augue nisi quis lacus Ut ac mi quis lacus mollis aliquam Curabitur iaculis tempus eros Curabitur</p>
  <div class="btn-white">Learn More</div>
</article>
<article class="abs card" style="left:782px">
  <div class="card-photo" role="img" aria-label="Technician working on top of an elevator car" style="background:linear-gradient(160deg,#c8c8c8,#8d8d8d 55%,#5d5d5d)"></div>
  <h3>Other Services</h3>
  <p>consectetuer augue nisi quis lacus Ut ac mi quis lacus mollis aliquam Curabitur iaculis tempus eros Curabitur</p>
  <div class="btn-white">Learn More</div>
</article>

<h2 class="abs head gallery-title">Our Gallery</h2>
<section class="abs gallery">
  <div role="img" aria-label="Office towers at night" style="background:linear-gradient(160deg,#0f1a1e,#3d5f66 60%,#1b2a2e)"></div>
  <div role="img" aria-label="Blue glass skyscraper" style="background:linear-gradient(160deg,#c9dbf2,#2e5fae 55%,#16346e)"></div>
  <div role="img" aria-label="Skyscrapers with sun and clouds" style="background:linear-gradient(160deg,#e8eef7,#4f7fc4 50%,#1d3c78)"></div>
  <div role="img" aria-label="Glass towers at dusk" style="background:linear-gradient(160deg,#3c6fb8,#4a8a9a 55%,#1d3250)"></div>
  <div role="img" aria-label="Tall tower under a cloudy sky" style="background:linear-gradient(160deg,#dfe9f5,#5d86b8 55%,#2a4d7a)"></div>
  <div role="img" aria-label="Looking up at blue glass towers" style="background:linear-gradient(160deg,#1f4e8a,#3f8bb8 55%,#8fb9d8)"></div>
</section>

<section class="abs contact-band" role="img" aria-label="Black and white aerial view of downtown towers"></section>
<div class="abs contact-box">
  <h2 class="head">Contact Us</h2>
  <p>Augiat in pede Fusce tellus Sed metus augue convallis et vehicula ut pulvinar eu ante Integer orci</p>
  <div class="btn-orange">Email Us</div>
  <div class="call">or Call Us (416) 555 0247</div>
</div>

<footer>
  <div class="abs footer"></div>
  <div class="abs footer-brand"><span class="brand-dot"></span>BRIGHTMOOR LIFT INC</div>
  <p class="abs footer-about">Augiat in pede Fusce tellus Sed metus augue convallis et vehicula ut pulvinar eu ante Integer orci tellus tristiqu</p>

  <h4 class="abs f-title" style="left:444px;top:3082px">Contact</h4>
  <ul class="abs f-list contact-list" style="left:448px;top:3127px">
    <li><svg width="18" height="18" viewBox="0 0 24 24"><path fill="#fff" d="M6.6 10.8a15 15 0 0 0 6.6 6.6l2.2-2.2c.3-.3.7-.4 1-.2 1.1.4 2.3.6 3.6.6.6 0 1 .4 1 1V20c0 .6-.4 1-1 1A17 17 0 0 1 3 4c0-.6.4-1 1-1h3.5c.6 0 1 .4 1 1 0 1.3.2 2.5.6 3.6.1.3 0 .7-.2 1z"/></svg>Phone (416) 555 0182</li>
    <li><svg width="18" height="22" viewBox="0 0 18 22"><rect x="3" y="1" width="12" height="20" rx="2" fill="none" stroke="#fff" stroke-width="2"/><circle cx="9" cy="17" r="1.3" fill="#fff"/></svg>Cell (905) 555 0139</li>
    <li><svg width="18" height="14" viewBox="0 0 18 14"><rect width="18" height="14" fill="#fff"/><path d="M0 0l9 7 9-7" fill="none" stroke="#0b0b0b" stroke-width="1.5"/></svg>office@brightmoorlift.ca</li>
  </ul>

  <h4 class="abs f-title" style="left:737px;top:3082px">Company</h4>
  <ul class="abs f-list company-list" style="left:739px;top:3118px">
    <li>About</li><li>Services</li><li>Blogs</li><li>Gallery</li><li>Contact Us</li>
  </ul>

  <h4 class="abs f-title" style="left:890px;top:3082px">Subscribe</h4>
  <div class="abs sub-input"><span>Email address</span><i><svg width="16" height="16" viewBox="0 0 16 16"><path d="M15 1 1 7l6 2 2 6z" fill="#fff"/></svg></i></div>
  <span class="abs social" style="left:887px"></span>
  <span class="abs social" style="left:942px"></span>
  <span class="abs social" style="left:997px"></span>
  <span class="abs social" style="left:1052px"></span>

  <div class="abs bottom-bar">© 2020 Company Name | All Rights Reserved</div>
</footer>

</body>
</html>
```